Yard sign

Looking for a yard sign. <br/>Something simple, name, number. <br/>Large text, readable from 50 feet away. <br/><br/>18 x 24 inches.

Target Market(s)

Potential homeowners thinking about going solar.

Colors

Designer to choose colors to be used in the design.

Requirements
Must have
• "WE'VE GONE SOLAR!"
Nice to have
• We are a solar company, we would like a design that compliments the homeowners decision that they went solar and encourages others to do the same.

```html
<!DOCTYPE html>
<html lang="en">
<head>
<meta charset="utf-8">
<title>We've Gone Solar! – Yard Sign</title>
<link rel="stylesheet" href="https://fonts.googleapis.com/css2?family=Poppins:wght@600&display=swap">
<style>
  :root {
    --sun-orange: #F39325;
    --sign-white: #FFFFFF;
  }
  html, body {
    margin: 0;
    padding: 0;
    width: 1200px;
    height: 900px;
    overflow: hidden;
    background: var(--sign-white);
  }
  .yard-sign {
    display: block;
    width: 1200px;
    height: 900px;
    font-family: "Poppins", "Century Gothic", sans-serif;
    font-weight: 600;
  }
  .headline { fill: var(--sun-orange); }
  .orange-band { fill: var(--sun-orange); }
  .sun-letter { fill: none; stroke: var(--sun-orange); stroke-width: 44; }
  .contact { fill: var(--sign-white); }
  .brand-dot { fill: var(--sign-white); }
</style>
</head>
<body>
<svg class="yard-sign" viewBox="0 0 1200 900" xmlns="http://www.w3.org/2000/svg">
  <!-- Headline -->
  <text class="headline headline-top" x="120" y="208" font-size="160"
        textLength="960" lengthAdjust="spacingAndGlyphs">WE'VE GONE</text>

  <g class="headline-solar" aria-label="SOLAR!">
    <text class="headline" x="112" y="455" font-size="300"
          textLength="140" lengthAdjust="spacingAndGlyphs">S</text>
    <circle class="sun-letter" cx="430" cy="352" r="92"
            role="img" aria-label="Sun illustration forming the letter O"/>
    <text class="headline" x="522" y="455" font-size="300"
          textLength="560" lengthAdjust="spacingAndGlyphs">LAR!</text>
  </g>

  <!-- Curved bottom band -->
  <path class="orange-band" d="M0 430 Q600 710 1200 430 L1200 900 L0 900 Z"/>

  <!-- Brand -->
  <g class="brand">
    <circle class="brand-dot" cx="78" cy="718" r="30"/>
    <text class="contact brand-name" x="124" y="712" font-size="44"
          textLength="238" lengthAdjust="spacingAndGlyphs">SUNRIDGE</text>
    <text class="contact brand-name" x="124" y="762" font-size="44"
          textLength="150" lengthAdjust="spacingAndGlyphs">SOLAR</text>
  </g>

  <!-- Contact details -->
  <text class="contact phone" x="412" y="730" font-size="118"
        textLength="733" lengthAdjust="spacingAndGlyphs">555-014-2738</text>
  <text class="contact website" x="412" y="792" font-size="62"
        textLength="678" lengthAdjust="spacingAndGlyphs">www.sunridgesolar.com</text>
</svg>
</body>
</html>
```